Create website for home automation - Control your lighting, fans, blinds etc remotely by smartphone

Plan for SHOPIFY Website - Our Clever Dwelling
Company name: Our Clever Dwelling
Company Slogan: Calm Evenings Come Naturally
Clean, Modern, Easy to Navigate, easy to maintain - not a lot of coding. We need flash technology but displaying simply what we do.
What we provide:
We will be offering wireless switch which can be added to iOS/Android App via WiFi, allowing users to remotely turn on/off connected lights, fans, security cameras, appliances, irrigation, humidifier separately from anywhere at any time.
Control your home away from home. No more wandering of your mind on those lights or appliances which you might have left switched on. No need to drive back home to check and switch them off. Save that energy, money and time just with a click of your phone no matter how far you are from home.
Replace your home electrical switches with smart switches. They retrofit existing electrical switches and allow you to make the transformation as needed.
Easy to use and intuitive app allows you to control your lights and devices just at a click. Set any kind of ambiance suiting your occasion.
Set scenes in smartphone app to group and operate your devices just at a button click. Same device can be included in more than one scene.
Collections and Products
Light Switches
Wall Plugs
Fan Switch
Pendants etc special lighting types.
Light Dimmers
Blind Controllers
Home Page:
Home page needs to telling customers what we do and how we do it in a few words to grab people.
Phone
Email
Support – Download instructions per product
Client login
Wholesale login
Promotional video to be on home screen - this is a short 1.5 - 2 min illustration introduction video to who we are and what we do - this is yet to be created)
Social media link - Facebook
Pages:
FAQ
About Us
Support/Shipping/Returns policy
Support/Installation
Blog posts
Product pages:
Description
Price
Space for where a video will be featured - how each product works/installation.
Reviews
Our competition:
http://www.brivo.com.au
https://lumigardenhub.com.au/2018/04/05/best-smart-light-switches-and-plugs/
https://www.tavelinq.com

```html
<!DOCTYPE html>
<html lang="en">
<head>
<meta charset="utf-8">
<title>Products – Our Clever Dwelling</title>
<link href="https://fonts.googleapis.com/css2?family=Montserrat:wght@300;400;500;700&display=swap" rel="stylesheet">
<style>
  :root{
    --ink:#1d1d1f;
    --body:#555;
    --navy:#0d2a7a;
    --link:#1463b4;
    --rule:#9a9a9a;
    --hero-a:#c9c9c9;
    --hero-b:#e2e2e2;
    --footer:#2b2b2b;
    --icon:#1877c9;
    --white:#fff;
  }
  *{margin:0;padding:0;box-sizing:border-box}
  html,body{width:960px;height:1200px;overflow:hidden;background:var(--white)}
  body{position:relative;font-family:"Montserrat",Arial,sans-serif;color:var(--ink)}
  .abs{position:absolute}

  .brand{left:240px;top:10px;width:120px;height:42px;display:flex;flex-direction:column;align-items:center}
  .brand-mark{width:16px;height:16px;background:var(--navy);margin-bottom:5px}
  .brand-name{font-size:7.4px;font-weight:700;color:var(--navy);letter-spacing:.2px;white-space:nowrap}
  .brand-slogan{font-size:3.8px;font-weight:400;color:var(--navy);letter-spacing:.4px;margin-top:1px;white-space:nowrap}

  .main-nav{left:434px;top:25px;display:flex;gap:18px;font-size:7.4px;color:#333}

  .hero{left:158px;top:62px;width:645px;height:171px;background:linear-gradient(100deg,var(--hero-a) 0%,var(--hero-b) 55%,#d4d4d4 100%);box-shadow:inset 0 2px 3px rgba(0,0,0,.15)}
  .hero-title{left:265px;top:124px;font-size:29px;font-weight:300;color:var(--white);letter-spacing:.5px}
  .hero-product{left:544px;top:96px;width:176px;height:116px;background:linear-gradient(160deg,#2a2a2a,#0f0f0f);transform:skewY(14deg);border-radius:2px}

  .product-img{background:linear-gradient(135deg,#fafafa 0%,#ececec 60%,#c9c9c9 100%);border-radius:3px}

  .product h2{font-size:11.2px;font-weight:500;letter-spacing:.2px;color:var(--ink)}
  .product p{font-size:7.4px;font-weight:300;line-height:11.6px;color:var(--body);margin-top:12px}
  .product .buy{display:block;font-size:7.6px;font-weight:400;color:var(--link);text-decoration:none;margin-top:8px}
  .product.right{text-align:right}

  .rule{left:242px;width:478px;height:1px;background:var(--rule)}

  .site-footer{left:158px;top:1062px;width:645px;height:138px;background:var(--footer)}
  .footer-nav{left:315px;top:1087px;display:flex;gap:17px;font-size:7.2px;color:var(--white)}
  .social{left:422px;top:1117px;display:flex;gap:5px}
  .social span{width:12px;height:12px;background:var(--icon);display:block}
  .legal{left:158px;top:1143px;width:645px;text-align:center;font-size:7px;line-height:9.6px;color:var(--white)}
</style>
</head>
<body>

<header>
  <div class="brand abs">
    <span class="brand-mark"></span>
    <span class="brand-name">OUR CLEVER DWELLING</span>
    <span class="brand-slogan">Calm Evenings Come Naturally</span>
  </div>
  <nav class="main-nav abs">
    <span>About Us</span><span>Products</span><span>Shipping</span><span>Support</span><span>Blog</span><span>Contact Us</span><span>Login</span>
  </nav>
</header>

<section class="hero abs" role="img" aria-label="Soft grey floral patterned banner background"></section>
<div class="hero-product abs" role="img" aria-label="Black glass smart switch panel"></div>
<h1 class="hero-title abs">PRODUCTS</h1>

<article class="product abs" style="left:272px;top:290px;width:260px">
  <h2>SMART POWER SWITCHES</h2>
  <p>Smart switches are at heart of our home automation solution.<br>These devices are available in one, two and three gangs. Our smart<br>switches retrofit existing electrical points and connect directly<br>to your home wi-fi router. Once connected, these can be easily<br>controlled by smart phone app. Additionally, all these switches<br>are available in custom colours or any custom print.</p>
  <a class="buy" href="#">BUY NOW &gt;&gt;</a>
</article>
<div class="product-img abs" style="left:578px;top:262px;width:102px;height:150px" role="img" aria-label="White one-gang smart power switch"></div>

<div class="rule abs" style="top:433px"></div>

<div class="product-img abs" style="left:276px;top:450px;width:94px;height:142px" role="img" aria-label="White smart light dimmer switch"></div>
<article class="product right abs" style="left:420px;top:469px;width:264px">
  <h2>SMART LIGHT DIMMERS</h2>
  <p>Smart switches are at heart of our home automation solution.<br>These devices are available in one, two and three gangs. Our smart<br>switches retrofit existing electrical points and connect directly<br>to your home wi-fi router. Once connected, these can be easily<br>controlled by smart phone app. Additionally, all these switches<br>are available in custom colours or any custom print.</p>
  <a class="buy" href="#">BUY NOW &gt;&gt;</a>
</article>

<div class="rule abs" style="top:618px"></div>

<article class="product abs" style="left:272px;top:668px;width:260px">
  <h2>SMART FAN SWITCHES</h2>
  <p>Smart switches are at heart of our home automation solution.<br>These devices are available in one, two and three gangs. Our smart<br>switches retrofit existing electrical points and connect directly<br>to your home wi-fi router. Once connected, these can be easily<br>controlled by smart phone app. Additionally, all these switches<br>are available in custom colours or any custom print.</p>
  <a class="buy" href="#">BUY NOW &gt;&gt;</a>
</article>
<div class="product-img abs" style="left:580px;top:641px;width:100px;height:150px" role="img" aria-label="White smart fan switch with three buttons"></div>

<div class="rule abs" style="top:816px"></div>

<div class="product-img abs" style="left:278px;top:841px;width:110px;height:162px" role="img" aria-label="White smart blind controller switch"></div>
<article class="product right abs" style="left:420px;top:868px;width:264px">
  <h2>SMART BLIND CONTROLLER</h2>
  <p>Smart switches are at heart of our home automation solution.<br>These devices are available in one, two and three gangs. Our smart<br>switches retrofit existing electrical points and connect directly<br>to your home wi-fi router. Once connected, these can be easily<br>controlled by smart phone app. Additionally, all these switches<br>are available in custom colours or any custom print.</p>
  <a class="buy" href="#">BUY NOW &gt;&gt;</a>
</article>

<footer class="site-footer abs"></footer>
<nav class="footer-nav abs">
  <span>Home</span><span>About Us</span><span>Products</span><span>Shipping</span><span>Support</span><span>Blog</span><span>Contact Us</span><span>Login</span>
</nav>
<div class="social abs" aria-label="Social links">
  <span></span><span></span><span></span><span></span><span></span><span></span><span></span>
</div>
<div class="legal abs">
  ABN: 47 315 902 118<br>
  Office: 4/22 Wattle Lane BRENTFORD NSW 2199<br>
  Telephone: (02) 5550 1834
</div>

</body>
</html>
```